Landscaping flier 2024

Create a 1 page flier for landscaping services
1. Must be completed in Adobe Photoshop
2. Size 8.5" x 11" (portrait layout)
3. Include logo
4. Text to include:
2024 Gravesite Landscaping Packages
info@hollowbrookmemorial.org
(201) 555-0148
hollowbrookmemorial.org
5. Use chart text for the content. DO NOT COPY THE CHART DESIGN/FORMAT. Use the chart for the text you need only.
6. Use "Pricing cards as format for laying out the chart". Open to other ideas as well.
**Use the example of chart design (handwritten) to base your design off of.
7. Photos
-include before and after care photos

```html
<!DOCTYPE html>
<html lang="en">
<head>
<meta charset="utf-8">
<title>Hollowbrook Memorial – 2024 Gravesite Landscaping Packages</title>
<link rel="stylesheet" href="https://fonts.googleapis.com/css2?family=Montserrat:wght@500;600;700;800&family=Oswald:wght@300;400&family=Bebas+Neue&display=swap">
<style>
:root{
  --red:#8c1a1f;
  --red-dark:#6a1014;
  --pink:#fde0e4;
  --pink-band:#fdd3d7;
  --gray-row:#e9eaec;
  --gray-dark:#5c5d61;
  --ink:#111;
  --icon-gray:#6d6e72;
}
*{box-sizing:border-box;margin:0;padding:0}
html,body{width:963px;height:1200px;overflow:hidden;background:#fff}
body{font-family:"Montserrat",sans-serif;color:var(--ink);position:relative}
.photo{position:absolute;top:0;height:460px}
.photo--before{left:0;width:480px;background:linear-gradient(180deg,#9aa3a0 0%,#7e8a82 22%,#4f8a2c 40%,#6ea83a 70%,#5d9a30 100%)}
.photo--after{left:483px;width:480px;background:linear-gradient(180deg,#8f9a95 0%,#76837c 24%,#4f8a2c 42%,#74ad3d 72%,#66a235 100%)}
.frame{position:absolute;left:34px;top:482px;width:902px;height:693px;border:1px solid var(--red);border-radius:20px}
.footer-band{position:absolute;left:0;top:1110px;width:963px;height:90px;background:var(--pink-band);border-radius:24px 24px 0 0}
.footer-text{position:absolute;left:0;top:1128px;width:963px;text-align:center;font-weight:700;font-size:20px;color:var(--red)}
.brand{position:absolute;left:68px;top:350px;width:178px;height:190px;background:#fff;border-radius:50% 50% 0 0;display:flex;flex-direction:column;align-items:center;justify-content:flex-end;padding-bottom:8px}
.brand-dot{width:54px;height:54px;border-radius:50%;border:2px solid var(--red);margin-bottom:12px}
.brand-name{font-weight:700;color:var(--red);font-size:21px;line-height:1.1;text-align:center;letter-spacing:.5px}
.table-bg{position:absolute;left:65px;top:551px;width:832px;height:547px;background:var(--gray-row)}
.ribbon{position:absolute;left:218px;top:473px;width:505px;height:116px}
.ribbon-year{position:absolute;left:218px;top:485px;width:505px;text-align:center;color:#fff;font-weight:800;font-size:32px;line-height:1.1}
.ribbon-line1{position:absolute;left:218px;top:520px;width:505px;text-align:center;color:#fff;font-weight:700;font-size:19px;line-height:1.2}
.ribbon-line2{position:absolute;left:218px;top:541px;width:505px;text-align:center;color:#fff;font-weight:800;font-size:25px;line-height:1.2}
.services-tab{position:absolute;left:65px;top:580px;width:222px;height:73px;background:var(--gray-dark);clip-path:polygon(0 0,70% 0,82% 32%,100% 32%,100% 100%,0 100%);color:#fff;font-family:"Oswald",sans-serif;font-weight:400;font-size:22px;line-height:.95;letter-spacing:1px;text-align:center;padding:17px 60px 0 0}
.services-tab span{display:block;padding-left:42px}
.plan-head{position:absolute;top:605px;width:201px;height:48px;background:#fff;border:2px solid var(--red);text-align:center;color:var(--red);padding-top:5px}
.plan-head .plan-name{font-weight:700;font-size:17px;line-height:1.05}
.plan-head .plan-sub{font-weight:600;font-size:11px}
.plan-head--seasonal{left:288px}
.plan-head--basic{left:490px}
.plan-head--perpetual{left:695px;top:587px;height:66px;border-color:var(--gray-dark);padding-top:18px}
.plan-head--perpetual .plan-name{font-size:19px}
.plan-head--perpetual .plan-sub{font-size:13px}
.popular-tab{position:absolute;left:700px;top:560px;width:192px;height:44px}
.popular-text{position:absolute;left:700px;top:566px;width:192px;text-align:center;color:#fff;font-family:"Bebas Neue",sans-serif;font-size:21px;letter-spacing:.5px}
.grid{position:absolute;left:65px;top:654px;width:832px;display:grid;grid-template-columns:222px 201px 201px 202px;column-gap:2px;background:#fff}
.cell{display:flex;align-items:center;justify-content:center;height:46.6px}
.row-white .cell{background:#fff}
.row-gray .cell{background:var(--gray-row)}
.row-white,.row-gray,.row-pink,.row-price{display:contents}
.label{justify-content:flex-start!important;padding-left:17px;font-weight:700;font-size:14.5px;line-height:1.05}
.row-pink .cell{background:var(--pink);height:70px;text-align:center;font-size:10.5px;font-weight:500;line-height:1.35}
.row-pink .label{justify-content:center!important;padding-left:0;font-size:15px;font-weight:700;line-height:1.05;flex-direction:column}
.row-price .cell{background:#fff;height:94px;flex-direction:column;font-size:9.5px;font-weight:500;text-align:center;line-height:1.3}
.row-price .valid{font-family:"Oswald",sans-serif;font-weight:300;font-size:14px;line-height:1;text-align:left;align-items:flex-start;justify-content:flex-end;padding:0 0 14px 20px}
.price-trio{display:flex;gap:4px;margin-bottom:6px}
.price-trio div{display:flex;flex-direction:column;align-items:center;color:var(--red)}
.price-trio b{background:var(--pink);padding:2px 5px;font-size:18px;font-weight:700}
.price-trio small{font-size:9.5px;margin-top:2px}
.price{background:var(--pink);color:var(--red);font-weight:700;padding:2px 6px;margin-bottom:8px}
.price--basic{font-size:21px}
.price--perpetual{font-size:26px}
.icon{width:22px;height:22px}
</style>
</head>
<body>
<div class="photo photo--before" role="img" aria-label="Before photo: overgrown, weedy gravesite in front of a granite family headstone"></div>
<div class="photo photo--after" role="img" aria-label="After photo: same gravesite neatly trimmed with a clipped boxwood bed and footstone"></div>

<div class="frame"></div>
<div class="footer-band"></div>
<p class="footer-text">48 Orchard Lane, Maple Glen NJ 07999 (201) 555-0148 | hollowbrookmemorial.org</p>

<div class="brand">
  <div class="brand-dot"></div>
  <p class="brand-name">HOLLOWBROOK<br>MEMORIAL</p>
</div>

<div class="table-bg"></div>

<svg class="ribbon" viewBox="0 0 505 116" aria-hidden="true">
  <polygon points="0,72 35,42 62,72" fill="var(--red-dark)"/>
  <polygon points="505,72 470,42 443,72" fill="var(--red-dark)"/>
  <ellipse cx="253" cy="50" rx="56" ry="50" fill="var(--red)"/>
  <path d="M42,42 H469 L446,100 Q440,114 420,114 H90 Q70,114 64,100 Z" fill="var(--red)"/>
</svg>
<p class="ribbon-year">2024</p>
<p class="ribbon-line1">GRAVESITE LANDSCAPING</p>
<p class="ribbon-line2">PACKAGES</p>

<div class="services-tab"><span>SERVICES</span>OFFERED</div>

<div class="plan-head plan-head--seasonal"><p class="plan-name">SEASONAL</p><p class="plan-sub">CARE ENDOWMENT</p></div>
<div class="plan-head plan-head--basic"><p class="plan-name">BASIC</p><p class="plan-sub">CARE ENDOWMENT</p></div>
<div class="plan-head plan-head--perpetual"><p class="plan-name">PERPETUAL</p><p class="plan-sub">CARE ENDOWMENT</p></div>
<svg class="popular-tab" viewBox="0 0 192 44" aria-hidden="true">
  <polygon points="0,44 14,12 30,12" fill="var(--red-dark)"/>
  <polygon points="192,44 178,12 162,12" fill="var(--red-dark)"/>
  <path d="M18,0 H174 L166,32 Q162,36 156,36 H36 Q30,36 26,32 Z" fill="var(--red)"/>
</svg>
<p class="popular-text">MOST POPULAR</p>

<svg width="0" height="0" style="position:absolute">
  <symbol id="tick" viewBox="0 0 22 22"><rect x="1" y="1" width="20" height="20" rx="3" fill="none" stroke="var(--red)" stroke-width="1.6"/><path d="M5.5,11 L9.5,16 L16.5,4.5" fill="none" stroke="var(--red)" stroke-width="1.6"/></symbol>
  <symbol id="cross" viewBox="0 0 22 22"><rect x="1" y="1" width="20" height="20" rx="3" fill="none" stroke="var(--icon-gray)" stroke-width="1.6"/><path d="M5.5,5.5 L16.5,16.5 M16.5,5.5 L5.5,16.5" stroke="var(--icon-gray)" stroke-width="1.6"/></symbol>
</svg>

<div class="grid">
  <div class="row-pink">
    <div class="cell label"><span>Weeding &amp; Trimming</span><span>on</span><span>Your Gravesite</span></div>
    <div class="cell">Approximately every 7 weeks<br>during the growing season :<br>Mid-April through Mid-October</div>
    <div class="cell">2 times per year :<br>Mid-May &amp;<br>Mid-September</div>
    <div class="cell">Approximately every 7 weeks<br>during the growing season :<br>Mid-April through Mid-October</div>
  </div>
  <div class="row-white">
    <div class="cell label">Payment Ensured<br>Forever Grave Care</div>
    <div class="cell"><svg class="icon"><use href="#cross"/></svg></div>
    <div class="cell"><svg class="icon"><use href="#tick"/></svg></div>
    <div class="cell"><svg class="icon"><use href="#tick"/></svg></div>
  </div>
  <div class="row-gray">
    <div class="cell label">Monument Leveling</div>
    <div class="cell"><svg class="icon"><use href="#cross"/></svg></div>
    <div class="cell"><svg class="icon"><use href="#tick"/></svg></div>
    <div class="cell"><svg class="icon"><use href="#tick"/></svg></div>
  </div>
  <div class="row-white">
    <div class="cell label">Monument Cleaning</div>
    <div class="cell"><svg class="icon"><use href="#cross"/></svg></div>
    <div class="cell"><svg class="icon"><use href="#cross"/></svg></div>
    <div class="cell"><svg class="icon"><use href="#tick"/></svg></div>
  </div>
  <div class="row-gray">
    <div class="cell label">Full Bed of Boxwood<br>Shrubs</div>
    <div class="cell"><svg class="icon"><use href="#cross"/></svg></div>
    <div class="cell"><svg class="icon"><use href="#cross"/></svg></div>
    <div class="cell"><svg class="icon"><use href="#tick"/></svg></div>
  </div>
  <div class="row-white">
    <div class="cell label">Replacement of Shrubs</div>
    <div class="cell"><svg class="icon"><use href="#cross"/></svg></div>
    <div class="cell"><svg class="icon"><use href="#cross"/></svg></div>
    <div class="cell"><svg class="icon"><use href="#tick"/></svg></div>
  </div>
  <div class="row-gray">
    <div class="cell label">Trust Certificate</div>
    <div class="cell"><svg class="icon"><use href="#cross"/></svg></div>
    <div class="cell"><svg class="icon"><use href="#cross"/></svg></div>
    <div class="cell"><svg class="icon"><use href="#tick"/></svg></div>
  </div>
  <div class="row-price">
    <div class="cell valid">Valid through<br>10.31.22</div>
    <div class="cell">
      <div class="price-trio">
        <div><b>$396</b><small>3 Years</small></div>
        <div><b>$264</b><small>2 Years</small></div>
        <div><b>$132</b><small>1 Year</small></div>
      </div>
      Multi-Year payment locks<br>in current rates
    </div>
    <div class="cell"><span class="price price--basic">$287</span>12 Monthly Payments.<br>Call for single payment discounts.</div>
    <div class="cell"><span class="price price--perpetual">$351</span>12 Monthly Payments.<br>Call for single payment discounts.</div>
  </div>
</div>
</body>
</html>
```